A design led business card for the construction industry

High-end business card to match logo. White logo on dark grey/off black to the front. Matching dark font on white to back, possibly with logo design again.

We offer construction and project management services to commercial and private clients in the UK. Projetcs range from newbuilds, conversion of listed buildings and refurbishments and extensions of existing homes. Our focus is on quality and attention to detail using the highest skills.

Contact Information for Business Card

Name; Dorian Keble BSc
Position; Project Manager
Mobile; 07962 408 175
Tel; 01632 960457
email; dorian@stonevale.co.uk
web; www.stonevale.co.uk
Address; Ashcombe on Wey, KX4 7PW

Colors

Designer to choose only greyscale colors for use in the design.

Requirements
Must have
• To include the below description of the business,

CONSTRUCTION - PROJECT MANAGEMENT
Nice to have
• The posibility of the top back of the card being used as a ruler. So will have a measurement to scale in mm or an architect scale of 1:50
Should not have
• Should not be portrait

```html
<!DOCTYPE html>
<html lang="en">
<head>
<meta charset="utf-8">
<title>Stonevale business card</title>
<link rel="stylesheet" href="https://fonts.googleapis.com/css2?family=Arimo:wght@400;700&display=swap">
<style>
  :root {
    --backdrop: #1b1b1b;
    --card: #0b0b0b;
    --ink: #ffffff;
    --silver: #c9c9c9;
    --rule: #4a4a4a;
  }
  * { box-sizing: border-box; margin: 0; padding: 0; }
  html, body {
    width: 1200px; height: 900px; overflow: hidden;
    background: var(--backdrop);
    font-family: "Arimo", Arial, sans-serif;
  }
  .canvas {
    width: 1200px; height: 900px;
    display: flex; align-items: center; justify-content: center; gap: 50px;
  }
  .card {
    width: 525px; height: 300px;
    background: var(--card);
    border-radius: 18px;
    position: relative;
    box-shadow: 0 12px 30px rgba(0,0,0,0.55);
  }
  /* contact side */
  .card-front { display: flex; align-items: center; padding: 0 34px; }
  .brand-block {
    width: 215px; display: flex; flex-direction: column; align-items: center; gap: 18px;
  }
  .brand-mark { width: 70px; height: 70px; border: 3px solid var(--ink); }
  .brand-name {
    color: var(--ink); font-size: 19px; font-weight: 400; letter-spacing: 9px;
    padding-left: 9px;
  }
  .divider { width: 1px; height: 150px; background: var(--rule); margin: 0 26px 0 18px; }
  .contact-block { color: var(--ink); }
  .person-name { font-size: 16px; font-weight: 700; text-transform: uppercase; }
  .person-name .credential { font-weight: 400; text-transform: none; }
  .person-role { font-size: 12px; margin-bottom: 14px; }
  .contact-list { list-style: none; font-size: 12px; line-height: 1.55; }
  .contact-list li { display: flex; align-items: center; gap: 7px; }
  .contact-list svg { width: 12px; height: 12px; flex: none; }
  .address { font-size: 12px; margin-top: 14px; }
  /* brand side */
  .card-back {
    display: flex; flex-direction: column; align-items: center; justify-content: center; gap: 22px;
  }
  .back-mark { width: 96px; height: 96px; border: 3px solid var(--silver); }
  .back-name {
    color: var(--silver); font-size: 28px; letter-spacing: 14px; padding-left: 14px;
  }
  .tagline {
    color: var(--silver); font-size: 11px; letter-spacing: 0.6px; margin-top: -10px;
  }
</style>
</head>
<body>
<main class="canvas">
  <section class="card card-front">
    <div class="brand-block">
      <div class="brand-mark"></div>
      <div class="brand-name">STONEVALE</div>
    </div>
    <div class="divider"></div>
    <div class="contact-block">
      <p class="person-name">Dorian Keble <span class="credential">BSc</span></p>
      <p class="person-role">Project Manager</p>
      <ul class="contact-list">
        <li>
          <svg viewBox="0 0 12 12" aria-hidden="true"><rect x="3" y="0.8" width="6" height="10.4" rx="1" fill="none" stroke="#fff" stroke-width="1.1"/><circle cx="6" cy="9.4" r="0.6" fill="#fff"/></svg>
          07962 408 175
        </li>
        <li>
          <svg viewBox="0 0 12 12" aria-hidden="true"><path d="M2.5 1.2 L4.6 1.2 L5.3 3.8 L4 4.8 Q5 7.2 7.2 8 L8.2 6.7 L10.8 7.4 L10.8 9.5 Q10.6 11 9 10.8 Q2 9.6 1.2 3 Q1.1 1.4 2.5 1.2 Z" fill="#fff"/></svg>
          01632 960457
        </li>
        <li>
          <svg viewBox="0 0 12 12" aria-hidden="true"><rect x="0.8" y="2.5" width="10.4" height="7" fill="none" stroke="#fff" stroke-width="1.1"/><path d="M0.8 2.5 L6 6.6 L11.2 2.5" fill="none" stroke="#fff" stroke-width="1.1"/></svg>
          dorian@stonevale.co.uk
        </li>
        <li>
          <svg viewBox="0 0 12 12" aria-hidden="true"><circle cx="6" cy="6" r="5" fill="none" stroke="#fff" stroke-width="1"/><ellipse cx="6" cy="6" rx="2.2" ry="5" fill="none" stroke="#fff" stroke-width="0.9"/><path d="M1 6 H11 M2 3.5 H10 M2 8.5 H10" stroke="#fff" stroke-width="0.8"/></svg>
          www.stonevale.co.uk
        </li>
      </ul>
      <p class="address">Ashcombe on Wey, KX4 7PW</p>
    </div>
  </section>

  <section class="card card-back">
    <div class="back-mark"></div>
    <div class="back-name">STONEVALE</div>
    <p class="tagline">CONSTRUCTION - PROJECT MANAGEMENT</p>
  </section>
</main>
</body>
</html>
```